A website where experts collaborate on your project

I am building a new website where experts (yes, like designers) collaborate on projects with the project owner. More minds = more collaboration = better end product. Please see Pelmora(dot)com for a quick landing page I created for collaborating on presentations (although there will be many project types offered)

I am looking for a DESIGNER LONG TERM, but for now, just need initial mock ups to show the web programmers.

I have 21 Word documents loosely designed, what I would like to see here is a theme. Please DO NOT GO OFF WHAT YOU CURRENTLY SEE AT PELMORA. What is up now is only a quick landing page.

You can view a Word doc of the homepage here:
https://www.filevanta.com/s/qx83kdm2/home.docx?dl=0

WHAT AM I LOOKING FOR?
A clean, well designed theme.

Here is a link to the logo:
https://www.filevanta.com/s/mr47tpz9/logo%20-%20horizontal.tif?dl=0
-----------------------------------------
Here are a few sites I like the design of and what I like about them:
www.quenbrook.com-all around my favorite, beautiful graphics, clean layout, bold use of colors on a dark background
Ravelto.com- clean layout, The use of humans and bubble style elements.
Mintharbor.com :) clean, bold, unique pop art style but professional
plumevault.com - From the unique colors and artwork and the ability of that art to not interfere with the important elements of the site
sparkwidgets.com-clean, nice colors, well organized and separated sections.
www.dunmereco.com-love the font, use of colors and sectionalized style

All in all, I am not picky and open to so many styles. I would ultimately like the designer I pick to design all 21 pages.
Updates

Hello everyone,Moving forward, I would like you all to pay special attention to the section in my brief titled "Here are a few sites I like the design of and what I like about them". Please see below, I handpicked each one of these as sites I really like. Thank you.Here are a few sites I like the design of and what I like about them:Ravelto.com- clean layout, The use of humans and bubble style elements.Mintharbor.com :) clean, bold, unique pop art style but professionalwriteraccess.com - From the unique colors and artwork and the ability of that art to not interfere with the important elements of the sitegrowthgeeks.com-clean, nice colors, well organized and separated sections.www.dunmereco.com-love the font, use of colors and sectionalized stylewww.quenbrook.com-beautiful graphics, clean layout, bold use of colors----------------------------------------- Added Tuesday, November 24, 2015

I updated the homepage, you can see it here:https://www.dropbox.com/s/kwlkbsookq3cg2m/1new%20homepage.docx?dl=0I am modeling it after my favorite designed site: triplelift.comI love the dark colors with the orange glowing style boldness of the buttons. It's real clean too. Added Tuesday, November 24, 2015

Target Market(s)

small business owners, marketers, freelancer writers, graphic designers,

Industry/Entity Type

Building

Number of Pages Required

5+ page

Requirements
Must have
• I can't think of anything the project must have.
Nice to have
• WHAT AM I LOOKING FOR?
• A clean, well designed theme. I had a designer do a bit of work putting elements together, I found it to be very plain, but I like the Application Page (https://www.filevanta.com/s/jb19ckr3/Pelmora-Website.ai?dl=0)
• Here is a link to the logo:
• https://www.filevanta.com/s/mr47tpz9/logo%20-%20horizontal.tif?dl=0
• Here are a few sites I like the design of and what I like about them:
• Ravelto.com- clean layout, The use of humans and bubble style elements.
• Mintharbor.com :) clean, bold, unique pop art style but professional
• plumevault.com - From the unique colors and artwork and the ability of that art to not interfere with the important elements of the site
• sparkwidgets.com-clean, nice colors, well organized and separated sections.
• www.dunmereco.com-love the font, use of colors and sectionalized style
• www.quenbrook.com-beautiful graphics, clean layout, bold use of colors
• -----------------------------------------
Should not have
• out of the boxed, templated style website. I want this site to be memorable and not look like a thousand others

```html
<!DOCTYPE html>
<html lang="en">
<head>
<meta charset="utf-8">
<title>Pelmora — Projects</title>
<link href="https://fonts.googleapis.com/css2?family=Open+Sans:ital,wght@0,400;0,600;0,700;1,400;1,600&display=swap" rel="stylesheet">
<style>
:root{
  --orange:#f7941d;
  --orange-dark:#e9820c;
  --header:#2e2e2e;
  --ink:#333333;
  --muted:#6f6f6f;
  --line:#d9d9d9;
  --footer:#ececec;
  --white:#ffffff;
}
*{box-sizing:border-box;margin:0;padding:0}
html,body{width:1200px;height:2542px;overflow:hidden}
body{position:relative;font-family:"Open Sans",Arial,sans-serif;color:var(--ink);background:var(--white)}
.abs{position:absolute}

/* header */
.site-header{position:absolute;left:0;top:0;width:1200px;height:112px;background:var(--header)}
.pill{position:absolute;top:56px;height:36px;border:1px solid #777;border-radius:18px;color:#bbb;font-size:11px;line-height:34px;padding-left:18px;text-transform:uppercase}
.browse{left:100px;width:115px}
.search{left:242px;width:228px}
.pill svg{position:absolute;right:14px;top:11px}
.header-note{left:498px;top:18px;color:#bdbdbd;font-size:10.5px;font-style:italic;line-height:19px}
.main-nav{left:498px;top:70px;display:flex;gap:0;font-size:12px;color:#fff;text-transform:uppercase}
.main-nav a{color:#fff;text-decoration:none;position:absolute;white-space:nowrap}
.main-nav a.active{color:var(--orange)}
.brand{left:864px;top:30px;height:60px;display:flex;align-items:center;gap:12px}
.brand-name{color:var(--orange);font-weight:700;font-size:32px;letter-spacing:-.5px}
.brand-dot{width:52px;height:52px;border-radius:50%;background:var(--orange)}

/* hero */
.hero{position:absolute;left:0;top:112px;width:1200px;height:529px;background:linear-gradient(180deg,#aab3b9 0%,#cfd3d4 38%,#9a9590 55%,#6d655e 100%)}
.hero-title{left:100px;top:162px;font-size:38px;font-weight:700;color:#2f2f2f}
.hero-sub{left:100px;top:215px;font-size:26px;line-height:37px;color:#3b3b3b;width:560px}
.btn{left:100px;top:307px;width:171px;height:45px;border-radius:23px;background:var(--orange);color:#fff;font-size:14px;font-weight:700;text-align:center;line-height:45px;text-transform:uppercase}
.dots{display:flex;gap:7px}
.dots i{width:9px;height:9px;border-radius:50%;background:#ddd;display:block}
.dots i.on{background:var(--orange)}

/* listing */
.section-title{font-size:23px;font-weight:700;color:var(--orange);text-transform:uppercase}
.filter-box{left:100px;top:739px;width:212px;height:417px;border:1px solid var(--line)}
.filter-row{position:absolute;left:0;width:210px;height:36px;border-top:1px solid var(--line);font-size:11px;font-weight:600;line-height:35px;padding-left:12px;text-transform:uppercase;color:#444}
.filter-row::after{content:"";position:absolute;right:10px;top:15px;border:5px solid transparent;border-top:6px solid #777}
.price-head{position:absolute;left:12px;top:10px;font-size:11px;font-weight:600;color:#444}
.price-head::after{content:"";position:absolute;left:181px;top:3px;border:5px solid transparent;border-left:6px solid #777}
.check{position:absolute;left:12px;font-size:11px;color:#555;display:flex;align-items:center;gap:14px}
.check i{width:13px;height:13px;border:1px solid #ccc;background:#f6f6f6;display:block}
.save-select{left:100px;top:1224px;width:212px;height:36px;border:1px solid var(--line);font-size:11px;font-weight:600;line-height:34px;padding-left:12px;color:#444}
.save-select::after{content:"";position:absolute;right:10px;top:14px;border:5px solid transparent;border-top:6px solid #777}
.sort{left:848px;top:700px;width:254px;font-size:11px;color:#555;text-align:right;text-transform:uppercase;word-spacing:2px}
.sort b{font-weight:600;color:#333}
.rule{height:1px;background:var(--line)}
.project{position:absolute;left:356px;width:746px;height:140px}
.project-thumb{position:absolute;left:0;top:0;width:205px;height:136px;border:1px solid var(--line);padding:7px;background:#fff}
.project-thumb div{width:100%;height:100%}
.project-title{position:absolute;left:244px;top:4px;width:480px;font-size:14px;font-weight:700;line-height:24px;text-transform:uppercase;color:#333}
.project-meta{position:absolute;left:244px;top:60px;display:flex;align-items:center;gap:8px;font-size:12px;color:#555}
.price{font-size:22px;font-weight:700;color:var(--orange)}
.price small{font-size:13px;color:#555;font-weight:600;margin-left:4px}
.time em{font-style:normal;color:var(--orange)}
.project-text{position:absolute;left:244px;top:100px;width:480px;font-size:11px;line-height:21px;color:#666}

/* testimonials */
.testimonials{position:absolute;left:0;top:1576px;width:1200px;height:443px;background:linear-gradient(180deg,#2a2623 0%,#3a332d 50%,#231f1c 100%)}
.t-title{left:0;top:62px;width:1200px;text-align:center;font-size:26px;font-weight:700;color:var(--orange);text-transform:uppercase}
.t-sub{left:0;top:108px;width:1200px;text-align:center;font-size:15px;color:#fff}
.avatar{width:110px;height:110px;border-radius:50%;border:4px solid #fff;background:#9b8a7c}
.quote{width:330px;font-size:11.5px;font-style:italic;line-height:23px;color:#fff}
.quote-mark{font-size:30px;color:#999;font-family:Georgia,serif}
.t-name{font-size:12px;font-weight:700;color:var(--orange);text-transform:uppercase}
.t-role{font-size:10.5px;font-style:italic;color:#fff}

/* clients */
.client{position:absolute;top:2076px;width:186px;height:109px;border:2px solid #e1e1e1;display:flex;align-items:center;justify-content:center;font-size:19px;font-weight:700;color:#2f5aa6}

/* footer */
.site-footer{position:absolute;left:0;top:2236px;width:1200px;height:239px;background:var(--footer)}
.f-head{font-size:14px;font-weight:700;color:var(--orange);text-transform:uppercase}
.f-text{font-size:11px;line-height:23px;color:#666}
.f-links{list-style:none;font-size:11px;color:#666;line-height:26px}
.social{display:flex;align-items:center;gap:8px;font-size:11px;color:#666}
.social i{width:30px;height:30px;border-radius:50%;display:block}
.copyright{left:0;top:2497px;width:1200px;text-align:center;font-size:11px;color:#666}
</style>
</head>
<body>

<header class="site-header">
  <div class="pill browse">Browse
    <svg width="10" height="8" viewBox="0 0 10 8"><path d="M1 2l4 4 4-4" fill="none" stroke="#bbb" stroke-width="1.5"/></svg>
  </div>
  <div class="pill search">Search
    <svg width="13" height="13" viewBox="0 0 13 13"><circle cx="5.5" cy="5.5" r="4.3" fill="none" stroke="#bbb" stroke-width="1.6"/><path d="M8.6 8.6l3.6 3.6" stroke="#bbb" stroke-width="1.8"/></svg>
  </div>
  <p class="abs header-note">Lorem Ipsum is simply dummy text of the printing and typesetting industry.<br>Lorem Ipsum has been the industry's standard</p>
  <nav class="abs main-nav">
    <a class="active" style="left:0">Projects</a>
    <a style="left:83px">How it works</a>
    <a style="left:197px">Plans</a>
    <a style="left:261px">My account</a>
  </nav>
  <div class="abs brand"><span class="brand-name">Pelmora</span><span class="brand-dot"></span></div>
</header>

<section class="hero" role="img" aria-label="Young man sitting on a wooden pier with a laptop under a cloudy sky">
  <h1 class="abs hero-title">Convert more customers</h1>
  <p class="abs hero-sub">Experience the power of experts collaborating on your project.</p>
  <div class="abs btn">Get started</div>
  <div class="abs dots" style="left:532px;top:511px"><i class="on"></i><i></i><i></i><i></i></div>
</section>

<h2 class="abs section-title" style="left:98px;top:689px">Filters</h2>
<div class="abs filter-box">
  <div class="price-head">PRICE</div>
  <div class="check" style="top:40px"><i></i>$1,000 - $2,000</div>
  <div class="check" style="top:69px"><i></i>$2,000 - $3,000</div>
  <div class="check" style="top:99px"><i></i>$3,000 - $4,000</div>
  <div class="check" style="top:130px"><i></i>$4,000 - $5,000</div>
  <div class="filter-row" style="top:164px">Country</div>
  <div class="filter-row" style="top:200px">Categories</div>
  <div class="filter-row" style="top:236px">Time left</div>
  <div class="filter-row" style="top:272px">Active | Expired</div>
  <div class="filter-row" style="top:308px">Contains adult content</div>
  <div class="filter-row" style="top:344px">Keywords</div>
  <div class="filter-row" style="top:380px">Followers</div>
</div>
<h2 class="abs section-title" style="left:98px;top:1177px">Save filters</h2>
<div class="abs save-select">SAVE FILTER</div>

<h2 class="abs section-title" style="left:356px;top:689px">Crowd projects</h2>
<p class="abs sort">Sort : <b>Price</b> &nbsp; / &nbsp; <b>Country</b> &nbsp; / &nbsp; <b>Time left</b></p>
<div class="abs rule" style="left:356px;top:736px;width:746px"></div>

<article class="project" style="top:773px">
  <div class="project-thumb"><div role="img" aria-label="Desktop, laptop, tablet and phone showing a website" style="background:linear-gradient(135deg,#dfeaf2,#9fb9cc)"></div></div>
  <h3 class="project-title">Lorem Ipsum is simply dummy text of the printing and typesetting industry</h3>
  <div class="project-meta"><span class="price">$80<small>UK</small></span><svg width="13" height="13" viewBox="0 0 13 13"><circle cx="6.5" cy="6.5" r="5.5" fill="none" stroke="#f7941d" stroke-width="1.6"/><path d="M6.5 3.5v3.2h2.4" fill="none" stroke="#f7941d" stroke-width="1.4"/></svg><span class="time">Time left : <em>6 days</em></span></div>
  <p class="project-text">Lorem Ipsum is simply dummy text of the printing and typesetting industry. Lorem Ipsum has been the industry's standard dummy text ever since the 1500s...</p>
</article>
<div class="abs rule" style="left:356px;top:941px;width:746px"></div>

<article class="project" style="top:970px">
  <div class="project-thumb"><div role="img" aria-label="Designer desk with colour swatches and a monitor" style="background:linear-gradient(135deg,#f2c4d8,#e8e8ea 55%,#b8c6d6)"></div></div>
  <h3 class="project-title">Lorem Ipsum is simply dummy text of the printing and typesetting industry</h3>
  <div class="project-meta"><span class="price">$80<small>UK</small></span><svg width="13" height="13" viewBox="0 0 13 13"><circle cx="6.5" cy="6.5" r="5.5" fill="none" stroke="#f7941d" stroke-width="1.6"/><path d="M6.5 3.5v3.2h2.4" fill="none" stroke="#f7941d" stroke-width="1.4"/></svg><span class="time">Time left : <em>6 days</em></span></div>
  <p class="project-text">Lorem Ipsum is simply dummy text of the printing and typesetting industry. Lorem Ipsum has been the industry's standard dummy text ever since the 1500s...</p>
</article>
<div class="abs rule" style="left:356px;top:1137px;width:746px"></div>

<article class="project" style="top:1166px">
  <div class="project-thumb"><div role="img" aria-label="Hands typing on a keyboard" style="background:linear-gradient(135deg,#2d5d74,#c9875a 60%,#7a4a32)"></div></div>
  <h3 class="project-title">Lorem Ipsum is simply dummy text of the printing and typesetting industry</h3>
  <div class="project-meta"><span class="price">$80<small>UK</small></span><svg width="13" height="13" viewBox="0 0 13 13"><circle cx="6.5" cy="6.5" r="5.5" fill="none" stroke="#f7941d" stroke-width="1.6"/><path d="M6.5 3.5v3.2h2.4" fill="none" stroke="#f7941d" stroke-width="1.4"/></svg><span class="time">Time left : <em>6 days</em></span></div>
  <p class="project-text">Lorem Ipsum is simply dummy text of the printing and typesetting industry. Lorem Ipsum has been the industry's standard dummy text ever since the 1500s...</p>
</article>
<div class="abs rule" style="left:356px;top:1336px;width:746px"></div>

<article class="project" style="top:1363px">
  <div class="project-thumb"><div role="img" aria-label="Word cloud of design terms on black" style="background:linear-gradient(135deg,#111,#3a3a3a 50%,#111)"></div></div>
  <h3 class="project-title">Lorem Ipsum is simply dummy text of the printing and typesetting industry</h3>
  <div class="project-meta"><span class="price">$80<small>UK</small></span><svg width="13" height="13" viewBox="0 0 13 13"><circle cx="6.5" cy="6.5" r="5.5" fill="none" stroke="#f7941d" stroke-width="1.6"/><path d="M6.5 3.5v3.2h2.4" fill="none" stroke="#f7941d" stroke-width="1.4"/></svg><span class="time">Time left : <em>6 days</em></span></div>
  <p class="project-text">Lorem Ipsum is simply dummy text of the printing and typesetting industry. Lorem Ipsum has been the industry's standard dummy text ever since the 1500s...</p>
</article>

<section class="testimonials" role="img" aria-label="Dimmed office scene with people working together">
  <h2 class="abs t-title">What our client's say</h2>
  <p class="abs t-sub">Lorem Ipsum is simply dummy text of the printing and typesetting industry has been the industry's standard...</p>

  <div class="abs avatar" style="left:101px;top:188px" role="img" aria-label="Client portrait"></div>
  <span class="abs quote-mark" style="left:246px;top:184px">&ldquo;</span>
  <p class="abs quote" style="left:259px;top:206px">With Pelmora I have multiple experts perfecting my content and I only pay for the feedback I find valuable. It's perfect...</p>
  <span class="abs quote-mark" style="left:598px;top:262px">&rdquo;</span>
  <p class="abs t-name" style="left:259px;top:288px">Dario Velt</p>
  <p class="abs t-role" style="left:259px;top:308px">CEO, Norvane 52</p>

  <div class="abs avatar" style="left:628px;top:188px" role="img" aria-label="Client portrait"></div>
  <span class="abs quote-mark" style="left:766px;top:184px">&ldquo;</span>
  <p class="abs quote" style="left:786px;top:206px;width:320px">Before you put any content in front of your audience, pelmora it with Pelmora, you won't regret it...</p>
  <span class="abs quote-mark" style="left:1083px;top:262px">&rdquo;</span>
  <p class="abs t-name" style="left:786px;top:288px">Ellis Marrow</p>
  <p class="abs t-role" style="left:786px;top:308px">CEO, Brightwell</p>

  <div class="abs dots" style="left:581px;top:368px"><i class="on"></i><i style="background:#888"></i><i style="background:#888"></i></div>
</section>

<div class="client" style="left:100px">Quilora</div>
<div class="client" style="left:305px">Tovan Archives</div>
<div class="client" style="left:510px">Verdani</div>
<div class="client" style="left:714px">Lumetto</div>
<div class="client" style="left:915px">Kestrel Books</div>

<footer class="site-footer">
  <h4 class="abs f-head" style="left:105px;top:46px">About Pelmora</h4>
  <p class="abs f-text" style="left:105px;top:78px;width:325px">Lorem Ipsum is simply dummy text of the printing and typesetting industry. Lorem Ipsum has been the industry's standard dummy text ever since the 1500s, when an unknown printer took a galley of type and scrambled it to make a type specimen book...</p>

  <h4 class="abs f-head" style="left:481px;top:46px">Welcome</h4>
  <ul class="abs f-links" style="left:481px;top:76px"><li>Projects</li><li>How it Works</li><li>Plans</li><li>My Account</li></ul>

  <h4 class="abs f-head" style="left:670px;top:46px">Information</h4>
  <ul class="abs f-links" style="left:670px;top:76px"><li>Terms &amp; Conditions</li><li>Privacy Policy</li><li>Disclaimer</li><li>Sitemap</li></ul>

  <h4 class="abs f-head" style="left:876px;top:46px">Follow us</h4>
  <div class="abs social" style="left:877px;top:83px"><i style="background:#3b5b98"></i>: Friendloop</div>
  <div class="abs social" style="left:1005px;top:83px"><i style="background:#3ba9dd"></i>: Chirpline</div>
  <div class="abs social" style="left:877px;top:129px"><i style="background:#1f78a9"></i>: Workfolio</div>
  <div class="abs social" style="left:1005px;top:129px"><i style="background:#f39a1e"></i>: RSS</div>
</footer>

<p class="abs copyright">© Copyrights, 2015. Pelmora. All rights reserved.</p>

</body>
</html>
```